Label Design for 2x Chutney Products

We need a label design for 2x Chutney Products.
Marigo Chutney - Red Chili
Marigo Chutney - Green Chili & Coriander
See attached pictures. This is just sample pictures so you get an impression of the product and the colors. Both labels to have as title the generic name "Marigo Chutney" and then added either Red Chili or Green Chili & Coriander. The different terms needs to be good readable and can differ in font/color/size, or in the same style if this makes more sense from design point (as I am not a designer). The labels later on need to be editable in the way that the ingredient list, nutrition list, basis company and production information can be added. If this needs to be done directly and cannot be edited later on please let know. Editable design related the additional text also would be good as the additional information need to be added in different languages (Dutch. German and perhaps French). No clue how this is to be implemented but looking forward to receive some input/solutions on this.
I already had a project to create the company logo. I consider this logo to be used as the product logo and not the company logo. A different company logo later on can be designed from new. This logo is here attached. Either to work with this logo and use it as product logo (perhaps revise the colors) and add the product description or create a new logo for the product from scratch if you feel too. The logo itself should be easily readable for the product name/description and the colors appealing to such product and of course customers.
Please contact if any clarification needed. Thanks in advance for your efforts and ideas for this project.

Industry/Entity Type

Food

Font styles to use
Other font styles liked:
• Asian Touch

Requirements
Nice to have
• If possible "simply" editable for text fields in order to add/revise the ingredient list, nutrition list, revise to different languages.

```html
<!DOCTYPE html>
<html lang="en">
<head>
<meta charset="utf-8">
<title>Marigo Chutney – Green Chili label</title>
<link rel="stylesheet" href="https://fonts.googleapis.com/css2?family=Baloo+2:wght@600;800&family=Montserrat:wght@700&display=swap">
<style>
  :root {
    --label-green: #176b04;
    --chili-green: #3f8f1f;
    --chili-shade: #2a7410;
    --title-lime: #8ef01c;
    --white: #ffffff;
    --tab-ink: #2a2a2a;
    --silver-light: #eef0f0;
    --silver-mid: #a9b0b2;
    --silver-dark: #6f777a;
  }
  * { margin: 0; padding: 0; box-sizing: border-box; }
  html, body { width: 1200px; height: 480px; overflow: hidden; background: var(--white); }
  .label {
    position: relative;
    width: 1200px;
    height: 480px;
    background: var(--label-green);
    overflow: hidden;
    font-family: "Baloo 2", sans-serif;
  }
  .foil-band {
    position: absolute;
    left: 0; width: 100%;
    height: 20px;
    background: linear-gradient(90deg, var(--silver-light) 0%, var(--silver-mid) 14%, var(--silver-light) 30%, var(--silver-dark) 50%, var(--silver-light) 66%, var(--silver-mid) 82%, var(--silver-light) 100%);
  }
  .foil-band--top { top: 0; box-shadow: 0 2px 4px rgba(0,0,0,.35); }
  .foil-band--bottom { bottom: 0; box-shadow: 0 -2px 4px rgba(0,0,0,.35); }

  .brand-tab {
    position: absolute;
    left: 557px; top: 19px;
    width: 86px; height: 136px;
    background: var(--white);
    border-radius: 0 0 22px 22px;
    display: flex;
    flex-direction: column;
    align-items: center;
    justify-content: flex-end;
    padding-bottom: 22px;
    gap: 10px;
  }
  .brand-tab__dot {
    width: 46px; height: 46px;
    border-radius: 50%;
    background: var(--label-green);
  }
  .brand-tab__name {
    font-family: "Montserrat", sans-serif;
    font-weight: 700;
    font-size: 13px;
    line-height: 1.05;
    color: var(--tab-ink);
    text-align: center;
    letter-spacing: .3px;
  }

  .chili-photo {
    position: absolute;
    background: radial-gradient(ellipse at 40% 40%, var(--chili-green), var(--chili-shade) 70%);
    opacity: .9;
  }
  .chili-photo--cluster {
    left: 190px; top: 290px; width: 290px; height: 130px;
    border-radius: 60% 40% 55% 45% / 50% 60% 40% 50%;
    transform: rotate(-14deg);
  }
  .chili-photo--right-tall {
    left: 1030px; top: 70px; width: 90px; height: 250px;
    border-radius: 50% 50% 50% 50% / 30% 30% 70% 70%;
    transform: rotate(18deg);
  }
  .chili-photo--faded-top {
    left: 895px; top: 19px; width: 80px; height: 160px;
    border-radius: 45% 45% 50% 50% / 30% 30% 70% 70%;
    transform: rotate(20deg);
    opacity: .45;
  }
  .chili-photo--faded-bottom {
    left: 895px; top: 300px; width: 80px; height: 160px;
    border-radius: 50% 50% 45% 45% / 40% 40% 60% 60%;
    transform: rotate(-18deg);
    opacity: .45;
  }

  .product-title {
    position: absolute;
    left: 380px; top: 166px;
    width: 420px;
    font-family: "Baloo 2", sans-serif;
    font-weight: 800;
    font-size: 86px;
    line-height: 80px;
    color: var(--title-lime);
    text-align: center;
  }
  .product-title__line { display: block; }

  .variant {
    position: absolute;
    left: 522px; top: 344px;
    font-family: "Baloo 2", sans-serif;
    font-weight: 600;
    font-size: 50px;
    line-height: 1;
    color: var(--white);
    letter-spacing: 1px;
  }
</style>
</head>
<body>
  <main class="label">
    <div class="foil-band foil-band--top"></div>

    <div class="chili-photo chili-photo--faded-top" role="img" aria-label="Photo of a green chili pepper, faded"></div>
    <div class="chili-photo chili-photo--faded-bottom" role="img" aria-label="Photo of a green chili pepper, faded"></div>
    <div class="chili-photo chili-photo--right-tall" role="img" aria-label="Photo of a long green chili pepper"></div>
    <div class="chili-photo chili-photo--cluster" role="img" aria-label="Photo of three crossed green chili peppers"></div>

    <div class="brand-tab">
      <span class="brand-tab__dot"></span>
      <span class="brand-tab__name">TARVEL<br>FOODS</span>
    </div>

    <h1 class="product-title">
      <span class="product-title__line">Marigo</span>
      <span class="product-title__line">Chutney</span>
    </h1>

    <p class="variant">Green Chili</p>

    <div class="foil-band foil-band--bottom"></div>
  </main>
</body>
</html>
```